Bookkeeping business needs a digital and print flyer

We need a flyer to promote our virtual bookkeeping services to small and mid-sized businesses in the United States. We want the content and design of the flyer to be consistent with our website: www.brightlanebookkeeping.example. We would like both a print version and a digital version of the flyer.

```html
<!DOCTYPE html>
<html lang="en">
<head>
<meta charset="utf-8">
<title>Bright Lane Bookkeeping – Virtual Bookkeeping Flyer</title>
<link rel="stylesheet" href="https://fonts.googleapis.com/css2?family=Montserrat:wght@400;500;700&family=Catamaran:wght@500;600;700&family=Open+Sans:ital,wght@1,400;1,700&display=swap">
<style>
:root{
  --yellow:#fbc232;
  --yellow-pale:#fde8a6;
  --yellow-ring:#fff1c6;
  --black:#0b0b0b;
  --charcoal:#3a3a3a;
  --white:#ffffff;
  --ink:#111111;
}
*{margin:0;padding:0;box-sizing:border-box}
html,body{width:848px;height:1200px;overflow:hidden;background:var(--white)}
.flyer{position:relative;width:848px;height:1200px;overflow:hidden;background:var(--white);color:var(--ink);font-family:"Catamaran",sans-serif}
.abs{position:absolute}
.left-panel{left:0;top:273px;width:405px;height:660px;background:linear-gradient(to bottom,var(--yellow) 0%,var(--yellow) 82%,#fde3a0 93%,var(--white) 100%)}
.divider-strip{left:405px;top:0;width:9px;height:930px;background:linear-gradient(to bottom,var(--yellow-pale) 85%,var(--white))}
.photo-desk{left:0;top:0;width:405px;height:273px;background:linear-gradient(135deg,#c98a3c 0%,#b5702a 45%,#e9b93a 70%,#d9a036 100%)}
.brand-header{left:425px;top:0;width:423px;height:273px;background:var(--black)}
.brand-name{left:481px;top:80px;font-family:"Montserrat",sans-serif;font-weight:400;font-size:33px;letter-spacing:1px;color:var(--white);white-space:nowrap}
.brand-sub{left:481px;top:123px;width:240px;text-align:right;font-family:"Montserrat",sans-serif;font-weight:400;font-size:14px;letter-spacing:1px;color:var(--white)}
.brand-dot{left:735px;top:94px;width:50px;height:50px;border-radius:50%;border:2px solid var(--white)}
.portrait{border-radius:50%}
.ring{border-radius:50%;background:var(--yellow-ring)}
.ring-inner{border-radius:50%;background:var(--yellow)}
h1.headline{left:53px;top:308px;font-family:"Montserrat",sans-serif;font-weight:700;line-height:1}
.headline .big{display:block;font-size:47px;letter-spacing:.5px}
.headline .mid{display:block;font-size:29px;margin-top:4px}
.headline .mid em{font-weight:500}
.tagline{left:53px;top:441px;font-family:"Montserrat",sans-serif;font-weight:500;font-size:12.5px;line-height:19px;letter-spacing:.4px}
.charge{left:53px;top:499px;font-family:"Montserrat",sans-serif;font-weight:700;font-size:22px;line-height:31.8px;letter-spacing:-.2px}
.bar{height:29px;background:linear-gradient(100deg,var(--black) 0%,var(--black) 55%,var(--charcoal) 56%,var(--charcoal) 100%);border:2px solid var(--black);font-family:"Catamaran",sans-serif;font-weight:700;line-height:27px;padding-left:9px}
.bar-outsource{left:55px;top:630px;width:311px;color:var(--yellow);font-size:18.5px}
.bar-services{left:476px;top:568px;width:311px;color:var(--white);font-size:18.5px;padding-left:13px}
.benefits{left:56px;top:664px;list-style:none;font-weight:600;font-size:14px}
.benefits li{height:24.3px;display:flex;align-items:center;gap:11px}
.benefits svg{flex:none}
.tailored{left:475px;top:505px;font-family:"Montserrat",sans-serif;font-weight:700;font-size:22px;line-height:31.5px;letter-spacing:-.2px}
.services{left:480px;top:609px;list-style:none;font-weight:500;font-size:13.6px;line-height:17px}
.services li{display:flex;gap:10px;margin-bottom:7.3px}
.services li.two{margin-bottom:7px}
.services .row{display:flex;gap:7px;align-items:center}
.services svg{flex:none;margin-top:1px}
.timeline{left:487px;top:624px;width:0;height:225px;border-left:1px dashed #444}
.note-shadow{left:37px;top:919px;width:770px;height:100px;border-radius:18px;background:rgba(0,0,0,.25);filter:blur(6px)}
.note{left:27px;top:913px;width:774px;height:98px;border-radius:16px;background:linear-gradient(100deg,var(--black) 0%,var(--black) 55%,#2f2f2f 56%,#2f2f2f 100%);border:2px solid var(--black);text-align:center;font-family:"Open Sans",sans-serif;font-style:italic;font-size:12.6px;line-height:21.5px;color:var(--white);padding-top:15px;padding-left:28px}
.note strong{color:var(--yellow);font-weight:700}
.waves{left:0;top:1030px}
.footer-cta{left:39px;top:1100px;font-size:14.5px;line-height:18px}
.footer-cta .lead{font-family:"Open Sans",sans-serif;font-style:italic}
.footer-cta .req{font-weight:700}
.phone-pill{left:39px;top:1147px;width:184px;height:29px;border-radius:15px;background:var(--black);color:var(--white);font-weight:700;font-size:20px;line-height:31px;padding-left:31px}
.phone-pill svg{position:absolute;left:5px;top:5px}
.vline{width:1px;height:66px;background:#333;top:1110px}
.contacts{left:346px;top:1107px;list-style:none;font-size:16px;font-weight:500}
.contacts li{height:23px;display:flex;align-items:center;gap:8px}
.follow{left:700px;top:1104px;width:92px;text-align:center;font-weight:700;font-size:16px}
.social{top:1131px;width:38px;height:38px;border-radius:50%;border:2px solid var(--black)}
</style>
</head>
<body>
<main class="flyer">

  <div class="abs left-panel"></div>
  <div class="abs divider-strip"></div>
  <div class="abs photo-desk" role="img" aria-label="Laptop and coffee cup on a yellow stool over a wooden floor"></div>

  <header class="abs brand-header"></header>
  <div class="abs brand-name">BRIGHT LANE</div>
  <div class="abs brand-sub">BOOKKEEPING</div>
  <div class="abs brand-dot"></div>

  <!-- portrait circles -->
  <div class="abs ring" style="left:353px;top:326px;width:174px;height:174px"></div>
  <div class="abs ring-inner" style="left:361px;top:334px;width:158px;height:158px"></div>
  <div class="abs portrait" role="img" aria-label="Businessman in a white shirt leaning on a desk with rubber ducks" style="left:368px;top:341px;width:144px;height:144px;background:linear-gradient(160deg,#f4f4f4,#dcdcdc 70%,#c9c9c9)"></div>

  <div class="abs ring" style="left:489px;top:217px;width:268px;height:268px"></div>
  <div class="abs ring-inner" style="left:502px;top:230px;width:242px;height:242px"></div>
  <div class="abs portrait" role="img" aria-label="Portrait of the bookkeeper in a navy blouse" style="left:522px;top:250px;width:202px;height:202px;background:radial-gradient(circle at 50% 60%,#2a3350 0%,#1f2740 45%,var(--yellow) 46%)"></div>

  <div class="abs ring" style="left:703px;top:309px;width:138px;height:138px"></div>
  <div class="abs ring-inner" style="left:710px;top:316px;width:124px;height:124px"></div>
  <div class="abs portrait" role="img" aria-label="Stressed business owner at a cluttered desk" style="left:716px;top:322px;width:112px;height:112px;background:linear-gradient(140deg,#9aa6b8,#c7ccd4 60%,#e6e1d2)"></div>

  <h1 class="abs headline">
    <span class="big">VIRTUAL</span>
    <span class="mid">BOOKKEEPING <em>FOR</em></span>
    <span class="mid">SMALL BUSINESS</span>
  </h1>
  <p class="abs tagline">BUILD YOUR BUSINESS BY<br>FOCUSING ON WHAT YOU LOVE</p>
  <h2 class="abs charge">TAKE CHARGE OF YOUR<br>BUSINESS &amp; CONCENTRATE<br>ON YOUR STRENGTHS TO<br>BECOME ITS HERO!</h2>

  <div class="abs bar bar-outsource">Outsource your bookkeeping!</div>
  <ul class="abs benefits">
    <li><svg width="17" height="17" viewBox="0 0 17 17"><circle cx="8.5" cy="8.5" r="8.5" fill="#0b0b0b"/><path d="M4.6 8.7l2.7 2.6 5-5" stroke="#fbc232" stroke-width="2.2" fill="none"/></svg>Take back your time</li>
    <li><svg width="17" height="17" viewBox="0 0 17 17"><circle cx="8.5" cy="8.5" r="8.5" fill="#0b0b0b"/><path d="M4.6 8.7l2.7 2.6 5-5" stroke="#fbc232" stroke-width="2.2" fill="none"/></svg>Do more of what you love</li>
    <li><svg width="17" height="17" viewBox="0 0 17 17"><circle cx="8.5" cy="8.5" r="8.5" fill="#0b0b0b"/><path d="M4.6 8.7l2.7 2.6 5-5" stroke="#fbc232" stroke-width="2.2" fill="none"/></svg>Focus on your strengths and what you do best</li>
    <li><svg width="17" height="17" viewBox="0 0 17 17"><circle cx="8.5" cy="8.5" r="8.5" fill="#0b0b0b"/><path d="M4.6 8.7l2.7 2.6 5-5" stroke="#fbc232" stroke-width="2.2" fill="none"/></svg>Confidently make business decisions</li>
    <li><svg width="17" height="17" viewBox="0 0 17 17"><circle cx="8.5" cy="8.5" r="8.5" fill="#0b0b0b"/><path d="M4.6 8.7l2.7 2.6 5-5" stroke="#fbc232" stroke-width="2.2" fill="none"/></svg>Sail through tax time</li>
    <li><svg width="17" height="17" viewBox="0 0 17 17"><circle cx="8.5" cy="8.5" r="8.5" fill="#0b0b0b"/><path d="M4.6 8.7l2.7 2.6 5-5" stroke="#fbc232" stroke-width="2.2" fill="none"/></svg>Save over the expense of a full-time employee</li>
    <li><svg width="17" height="17" viewBox="0 0 17 17"><circle cx="8.5" cy="8.5" r="8.5" fill="#0b0b0b"/><path d="M4.6 8.7l2.7 2.6 5-5" stroke="#fbc232" stroke-width="2.2" fill="none"/></svg>Pay yourself more</li>
    <li><svg width="17" height="17" viewBox="0 0 17 17"><circle cx="8.5" cy="8.5" r="8.5" fill="#0b0b0b"/><path d="M4.6 8.7l2.7 2.6 5-5" stroke="#fbc232" stroke-width="2.2" fill="none"/></svg>Experience financial peace</li>
  </ul>

  <h2 class="abs tailored">BOOKKEEPING TAILORED<br>TO YOUR BUSINESS NEEDS</h2>
  <div class="abs bar bar-services">Services Available:</div>
  <div class="abs timeline"></div>
  <ul class="abs services">
    <li><svg width="15" height="15" viewBox="0 0 15 15"><circle cx="7.5" cy="7.5" r="7.5" fill="#fbc232"/><path d="M4 7.7l2.4 2.3 4.5-4.5" stroke="#fff" stroke-width="1.8" fill="none"/></svg>Catch-up and clean-up services</li>
    <li><svg width="15" height="15" viewBox="0 0 15 15"><circle cx="7.5" cy="7.5" r="7.5" fill="#fbc232"/><path d="M4 7.7l2.4 2.3 4.5-4.5" stroke="#fff" stroke-width="1.8" fill="none"/></svg>Transaction importation and categorization</li>
    <li class="two"><svg width="15" height="15" viewBox="0 0 15 15"><circle cx="7.5" cy="7.5" r="7.5" fill="#fbc232"/><path d="M4 7.7l2.4 2.3 4.5-4.5" stroke="#fff" stroke-width="1.8" fill="none"/></svg><span>Monthly reconciliation of all<br>accounts, including assets and loans.</span></li>
    <li class="two"><svg width="15" height="15" viewBox="0 0 15 15"><circle cx="7.5" cy="7.5" r="7.5" fill="#fbc232"/><path d="M4 7.7l2.4 2.3 4.5-4.5" stroke="#fff" stroke-width="1.8" fill="none"/></svg><span>Monthly financial reports (Balance Sheet,<br>Income Statement, Cash Flow)</span></li>
    <li><svg width="15" height="15" viewBox="0 0 15 15"><circle cx="7.5" cy="7.5" r="7.5" fill="#fbc232"/><path d="M4 7.7l2.4 2.3 4.5-4.5" stroke="#fff" stroke-width="1.8" fill="none"/></svg>Monthly video conference</li>
    <li><svg width="15" height="15" viewBox="0 0 15 15"><circle cx="7.5" cy="7.5" r="7.5" fill="#fbc232"/><path d="M4 7.7l2.4 2.3 4.5-4.5" stroke="#fff" stroke-width="1.8" fill="none"/></svg>Annual tax-prep package sent to your preparer</li>
    <li><svg width="15" height="15" viewBox="0 0 15 15"><circle cx="7.5" cy="7.5" r="7.5" fill="#fbc232"/><path d="M4 7.7l2.4 2.3 4.5-4.5" stroke="#fff" stroke-width="1.8" fill="none"/></svg><span class="row">A/R &amp; A/P <svg width="15" height="15" viewBox="0 0 15 15"><circle cx="7.5" cy="7.5" r="7.5" fill="#fbc232"/><path d="M4 7.7l2.4 2.3 4.5-4.5" stroke="#fff" stroke-width="1.8" fill="none"/></svg> Payroll coordination</span></li>
    <li><svg width="15" height="15" viewBox="0 0 15 15"><circle cx="7.5" cy="7.5" r="7.5" fill="#fbc232"/><path d="M4 7.7l2.4 2.3 4.5-4.5" stroke="#fff" stroke-width="1.8" fill="none"/></svg><span class="row">1099s <svg width="15" height="15" viewBox="0 0 15 15"><circle cx="7.5" cy="7.5" r="7.5" fill="#fbc232"/><path d="M4 7.7l2.4 2.3 4.5-4.5" stroke="#fff" stroke-width="1.8" fill="none"/></svg> Bill pay and receipt management</span></li>
    <li><svg width="15" height="15" viewBox="0 0 15 15"><circle cx="7.5" cy="7.5" r="7.5" fill="#fbc232"/><path d="M4 7.7l2.4 2.3 4.5-4.5" stroke="#fff" stroke-width="1.8" fill="none"/></svg>Budgeting</li>
  </ul>

  <div class="abs note-shadow"></div>
  <div class="abs note">
    Did you get into business because you loved recording finances?&nbsp; Reconciling bank statements?&nbsp; Prepping for taxes?<br>
    Of course not!&nbsp; Only nerdy bookkeepers enjoy these things.<br>
    <strong>You want to follow your passion, do what you do best to build a booming business.</strong>
  </div>

  <svg class="abs waves" width="848" height="170" viewBox="0 0 848 170">
    <path d="M0 35 C120 55 200 60 300 45 C420 25 520 30 620 48 C720 65 790 40 848 20 L848 170 L0 170Z" fill="#fff4d2"/>
    <path d="M0 45 C110 70 220 70 330 55 C450 38 540 45 640 62 C740 78 800 55 848 35 L848 170 L0 170Z" fill="#fde49a"/>
    <path d="M0 58 C130 82 230 80 340 66 C460 52 560 60 660 75 C750 88 810 70 848 52 L848 170 L0 170Z" fill="#fbc232"/>
  </svg>

  <div class="abs footer-cta">
    <div class="lead">Free Consultation Call</div>
    <div class="req">Request your free consultation</div>
  </div>
  <div class="abs phone-pill">
    <svg width="19" height="19" viewBox="0 0 19 19"><circle cx="9.5" cy="9.5" r="8.3" fill="none" stroke="#fbc232" stroke-width="2"/><path d="M6.3 5.2l1.6 1.9-1 1.2c.6 1.4 1.6 2.4 3 3l1.2-1 1.9 1.6-1 1.6c-3.4-.4-6.2-3.2-6.6-6.6z" fill="#fbc232"/></svg>
    555-014-2290
  </div>
  <div class="abs vline" style="left:319px"></div>
  <ul class="abs contacts">
    <li><svg width="10" height="14" viewBox="0 0 10 14"><path d="M5 0a5 5 0 0 1 5 5c0 3.5-5 9-5 9S0 8.5 0 5a5 5 0 0 1 5-5z" fill="#111"/><circle cx="5" cy="5" r="1.8" fill="#fbc232"/></svg>Cedar Ridge, NE</li>
    <li><svg width="12" height="9" viewBox="0 0 12 9"><rect width="12" height="9" fill="#111"/><path d="M0 0l6 5 6-5" stroke="#fbc232" stroke-width="1.2" fill="none"/></svg>hello@brightlanebookkeeping.example</li>
    <li><svg width="12" height="12" viewBox="0 0 12 12"><circle cx="6" cy="6" r="5.3" fill="none" stroke="#111" stroke-width="1.4"/><path d="M1 6h10M6 1c-2.5 3-2.5 7 0 10M6 1c2.5 3 2.5 7 0 10" stroke="#111" stroke-width="1" fill="none"/></svg>brightlanebookkeeping.example</li>
  </ul>
  <div class="abs vline" style="left:663px"></div>
  <div class="abs follow">Follow Us</div>
  <div class="abs social" style="left:706px"></div>
  <div class="abs social" style="left:750px"></div>

</main>
</body>
</html>
```